NEW Modern Sleek Business Card for VR Language Startup

Our startup is using VR to lead the next wave of world language education. We need a two-sided business card that introduces the larger organization (Brightloom Language Inc) and our contact info on one side and shows the product, Glimwoorld, on the other side.

Side 1 (contact info)= Brightloom Logo and Contact info (name, title, phone, email)

Side 2 (product)= Glimworld logo, text, and website
Text= Culturally Immersive Language Learning Games
Website= www.glimworld-play.com

Target Market(s)

Education, Technology

Contact Information for Business Card

Contact info will be updated upon approval of the design. For now, put this as a placeholder.

Perry Dunmore
Founder & CEO
pdunmore@quillpost-mail.net
(555)-014-2286

Font styles to use
Other font styles liked:
• Gibson and Century Gothic are the brand fonts

Requirements
Nice to have
• I would love to see cohesion between the design and colors of the two logos. I have attached a few business card designs that I like, so you can get a feel for my preferred style.

```html
<!DOCTYPE html>
<html lang="en">
<head>
<meta charset="utf-8">
<title>Brightloom Language – Business Card</title>
<link rel="stylesheet" href="https://fonts.googleapis.com/css2?family=Questrial&family=Roboto:wght@400;500;700&display=swap">
<style>
  :root {
    --backdrop: #e4e5e8;
    --card: #ffffff;
    --ink: #1b1b1f;
    --ink-soft: #3a3a40;
    --brand-blue: #2f8cf0;
    --brand-violet: #5b5cf0;
    --brand-orange: #ff6a2c;
    --brand-red: #f2334f;
    --brand-cyan: #19e0e6;
    --rule: #5a6ff0;
  }
  * { box-sizing: border-box; margin: 0; padding: 0; }
  html, body {
    width: 1200px;
    height: 800px;
    overflow: hidden;
    background: var(--backdrop);
  }
  .sheet {
    width: 1200px;
    height: 800px;
    display: flex;
    align-items: center;
    justify-content: center;
    gap: 60px;
  }
  .card {
    width: 525px;
    height: 300px;
    background: var(--card);
    position: relative;
    box-shadow: 0 10px 28px rgba(0,0,0,0.12);
  }

  /* Product side */
  .product-side {
    display: flex;
    flex-direction: column;
    align-items: center;
    justify-content: center;
    font-family: "Roboto", sans-serif;
  }
  .product-brands {
    display: flex;
    align-items: flex-end;
    gap: 46px;
    margin-bottom: 22px;
  }
  .product-name {
    font-family: "Questrial", sans-serif;
    font-size: 40px;
    color: var(--brand-violet);
    display: flex;
    align-items: center;
    gap: 10px;
  }
  .product-name .dot {
    width: 14px; height: 14px; border-radius: 50%;
    background: var(--brand-cyan);
  }
  .parent-name {
    font-family: "Questrial", sans-serif;
    font-size: 24px;
    letter-spacing: 2px;
    color: var(--ink);
    padding-bottom: 6px;
  }
  .tagline {
    font-style: italic;
    font-size: 14px;
    color: var(--ink-soft);
    margin-bottom: 10px;
  }
  .web-rule {
    display: flex;
    align-items: center;
    width: 440px;
  }
  .web-rule .line { flex: 1; height: 1px; background: linear-gradient(90deg, transparent, var(--rule)); }
  .web-rule .line.right { background: linear-gradient(90deg, var(--rule), transparent); }
  .web-rule .node {
    width: 8px; height: 8px; border-radius: 50%;
    border: 1.5px solid var(--rule);
    margin: 0 6px;
  }
  .website {
    font-size: 14px;
    color: var(--rule);
  }

  /* Contact side */
  .contact-side {
    font-family: "Roboto", sans-serif;
  }
  .brand-mark-area {
    position: absolute;
    left: 60px; top: 50px;
    width: 200px; height: 200px;
    border-radius: 50%;
    background: var(--brand-red);
  }
  .company-name {
    position: absolute;
    right: 40px; top: 96px;
    font-family: "Questrial", sans-serif;
    font-size: 36px;
    letter-spacing: 3px;
    color: var(--ink);
  }
  .contact-block {
    position: absolute;
    right: 40px; bottom: 40px;
    text-align: right;
  }
  .person-name {
    font-size: 20px;
    font-weight: 500;
    color: var(--brand-blue);
  }
  .person-title {
    font-size: 13px;
    color: var(--brand-orange);
    margin-bottom: 10px;
  }
  .contact-line {
    display: flex;
    align-items: center;
    justify-content: flex-end;
    gap: 8px;
    font-size: 12px;
    color: var(--ink);
    line-height: 1.6;
  }
  .contact-line svg { width: 11px; height: 11px; fill: var(--ink); }
</style>
</head>
<body>
<main class="sheet">

  <section class="card product-side" aria-label="Product side">
    <div class="product-brands">
      <div class="product-name"><span class="dot"></span>Glimworld</div>
      <div class="parent-name">Brightloom</div>
    </div>
    <p class="tagline">Culturally Immersive Language Learning Games</p>
    <div class="web-rule">
      <span class="line"></span>
      <span class="node"></span>
      <span class="website">www.glimworld-play.com</span>
      <span class="node"></span>
      <span class="line right"></span>
    </div>
  </section>

  <section class="card contact-side" aria-label="Contact side">
    <div class="brand-mark-area"></div>
    <div class="company-name">Brightloom</div>
    <div class="contact-block">
      <div class="person-name">Perry Dunmore</div>
      <div class="person-title">Founder &amp; CEO</div>
      <div class="contact-line">
        <span>(555)-014-2286</span>
        <svg viewBox="0 0 24 24" aria-hidden="true"><path d="M6.6 10.8a15.1 15.1 0 0 0 6.6 6.6l2.2-2.2a1 1 0 0 1 1-.25 11.4 11.4 0 0 0 3.6.57 1 1 0 0 1 1 1V20a1 1 0 0 1-1 1A17 17 0 0 1 3 4a1 1 0 0 1 1-1h3.5a1 1 0 0 1 1 1c0 1.25.2 2.45.57 3.57a1 1 0 0 1-.25 1z"/></svg>
      </div>
      <div class="contact-line">
        <span>pdunmore@quillpost-mail.net</span>
        <svg viewBox="0 0 24 24" aria-hidden="true"><path d="M2 5h20v14H2z M4 7v.5l8 5 8-5V7l-8 5z" fill-rule="evenodd"/></svg>
      </div>
    </div>
  </section>

</main>
</body>
</html>
```